Oil and Gas Exploration and Production company needs a business card design

We need a business card design using our logo and colors in the logo. We want a mainstream design.

```html
<!DOCTYPE html>
<html lang="en">
<head>
<meta charset="utf-8">
<title>Rava Oil &amp; Gas – Business Card</title>
<link rel="stylesheet" href="https://fonts.googleapis.com/css2?family=Arimo:wght@400;700&display=swap">
<style>
  :root {
    --page-bg: #e9e4dc;
    --card-dark: #141414;
    --card-dark-soft: #2b2b2b;
    --card-light: #e6e3de;
    --card-light-2: #cfd6dc;
    --gold: #a8690f;
    --gold-light: #c98a2a;
    --text-light: #f2f2f2;
    --text-muted: #d6d6d6;
    --contact-tint: #e4c9c2;
    --ink: #151515;
    --chip: #e8dccb;
  }
  html, body {
    margin: 0;
    padding: 0;
    width: 1200px;
    height: 970px;
    overflow: hidden;
    background: var(--page-bg);
    font-family: "Arimo", Arial, sans-serif;
  }
  .canvas {
    position: relative;
    width: 1200px;
    height: 970px;
  }
  .card {
    position: absolute;
    left: 80px;
    top: 190px;
    width: 1040px;
    height: 590px;
    border-radius: 30px;
    overflow: hidden;
    box-shadow: 0 18px 40px rgba(0,0,0,0.25);
  }
  .card-shapes {
    position: absolute;
    inset: 0;
    width: 1040px;
    height: 590px;
  }
  .holder {
    position: absolute;
    left: 62px;
    top: 88px;
  }
  .holder-name {
    margin: 0;
    font-size: 31px;
    font-weight: 700;
    color: var(--text-light);
    line-height: 1.05;
  }
  .holder-title {
    margin: 2px 0 0;
    font-size: 25px;
    font-weight: 400;
    color: var(--gold-light);
  }
  .address {
    position: absolute;
    left: 63px;
    top: 364px;
    margin: 0;
    font-style: normal;
    font-size: 24px;
    line-height: 33px;
    color: var(--text-muted);
  }
  .contacts {
    position: absolute;
    left: 60px;
    top: 444px;
    margin: 0;
    padding: 0;
    list-style: none;
  }
  .contacts li {
    display: flex;
    align-items: center;
    height: 35px;
    font-size: 24px;
    color: var(--contact-tint);
  }
  .contacts svg {
    width: 30px;
    height: 30px;
    margin-right: 12px;
    flex: none;
  }
  .brand {
    position: absolute;
    left: 572px;
    top: 70px;
    display: flex;
    align-items: center;
    gap: 18px;
  }
  .brand-dot {
    width: 58px;
    height: 58px;
    border-radius: 50%;
    background: var(--ink);
    flex: none;
  }
  .brand-name {
    margin: 0;
    font-weight: 700;
    color: var(--ink);
    line-height: 1;
  }
  .brand-name .brand-main {
    display: block;
    font-size: 112px;
    letter-spacing: -2px;
  }
  .brand-name .brand-sub {
    display: block;
    font-size: 36px;
    letter-spacing: 6px;
    margin-top: 4px;
    text-align: right;
  }
  .social {
    position: absolute;
    right: 52px;
    bottom: 46px;
    display: flex;
    gap: 10px;
  }
  .social span {
    width: 48px;
    height: 48px;
    border-radius: 50%;
    background: var(--chip);
    box-shadow: inset 0 -3px 4px rgba(0,0,0,0.25);
  }
</style>
</head>
<body>
<main class="canvas">
  <section class="card" aria-label="Rava Oil &amp; Gas business card">
    <svg class="card-shapes" viewBox="0 0 1040 590" aria-hidden="true">
      <defs>
        <linearGradient id="lightPanel" x1="0" y1="0" x2="1" y2="1">
          <stop offset="0" stop-color="#ece9e4"/>
          <stop offset="0.6" stop-color="#dcdcda"/>
          <stop offset="1" stop-color="#c9d2d8"/>
        </linearGradient>
        <linearGradient id="darkPanel" x1="0" y1="0" x2="1" y2="0.3">
          <stop offset="0" stop-color="#262626"/>
          <stop offset="0.5" stop-color="#141414"/>
          <stop offset="1" stop-color="#060606"/>
        </linearGradient>
        <linearGradient id="goldBand" x1="0" y1="0" x2="1" y2="1">
          <stop offset="0" stop-color="#b8740f"/>
          <stop offset="1" stop-color="#8a560c"/>
        </linearGradient>
      </defs>
      <rect class="light-panel" width="1040" height="590" fill="url(#lightPanel)"/>
      <path class="gold-band" fill="url(#goldBand)"
        d="M375,0 L432,0 C455,170 580,275 770,312 C905,338 1000,405 1040,455 L1040,495 L0,495 L0,0 Z"/>
      <path class="dark-panel" fill="url(#darkPanel)"
        d="M0,0 L378,0 C405,185 545,300 740,330 C880,352 985,415 1040,485 L1040,590 L0,590 Z"/>
    </svg>

    <header class="holder">
      <h1 class="holder-name">Daniel Marsh</h1>
      <p class="holder-title">President &amp; CEO</p>
    </header>

    <div class="brand">
      <span class="brand-dot"></span>
      <p class="brand-name">
        <span class="brand-main">Rava</span>
        <span class="brand-sub">OIL &amp; GAS</span>
      </p>
    </div>

    <address class="address">PO BOX 48, Harbour Road<br>West Quay, Bristol</address>

    <ul class="contacts">
      <li>
        <svg viewBox="0 0 30 30" aria-hidden="true">
          <circle cx="15" cy="15" r="13" fill="none" stroke="#a8690f" stroke-width="2"/>
          <path d="M10 9 l3 0 l1 3 l-2 1.5 a8 8 0 0 0 4 4 l1.5 -2 l3 1 l0 3 a1.5 1.5 0 0 1 -1.5 1.5 a11 11 0 0 1 -10.5 -10.5 a1.5 1.5 0 0 1 1.5 -1.5 z" fill="#a8690f"/>
        </svg>
        (044) 210 7781
      </li>
      <li>
        <svg viewBox="0 0 30 30" aria-hidden="true">
          <circle cx="15" cy="15" r="13" fill="none" stroke="#a8690f" stroke-width="2"/>
          <rect x="8" y="10" width="14" height="10" fill="none" stroke="#a8690f" stroke-width="1.8"/>
          <path d="M8 10 l7 6 l7 -6" fill="none" stroke="#a8690f" stroke-width="1.8"/>
        </svg>
        contact@ravaenergy.net
      </li>
      <li>
        <svg viewBox="0 0 30 30" aria-hidden="true">
          <circle cx="15" cy="15" r="13" fill="none" stroke="#a8690f" stroke-width="2"/>
          <circle cx="15" cy="15" r="7.5" fill="none" stroke="#a8690f" stroke-width="1.6"/>
          <ellipse cx="15" cy="15" rx="3.2" ry="7.5" fill="none" stroke="#a8690f" stroke-width="1.4"/>
          <path d="M7.5 15 h15 M9 11 h12 M9 19 h12" stroke="#a8690f" stroke-width="1.2"/>
        </svg>
        www.ravaenergy.net
      </li>
    </ul>

    <div class="social" aria-label="Social profiles">
      <span></span>
      <span></span>
    </div>
  </section>
</main>
</body>
</html>
```